Danielle Brooke Interiors business cards

We need a DOUBLE SIDED business card design that is simple, elegant and modern. We are a rapidly growing Interior Design Firm, and our brand colours are blush pink, navy, and antique gold, so we require some or all of these colours to be used. The final design should portray elegance, simplicity, and have a modern feel. We have upload inspiration photos that have the feel we're looking for.

Industry/Entity Type

Interior Design

Contact Information for Business Card

Contact information and LOGO

Colors
EB3D1F
EC4F4E
F09395
F8D3D4
FCEDEE

Requirements
Must have
• Navy, the right shade of blush pink, and antique gold

```html
<!DOCTYPE html>
<html lang="en">
<head>
<meta charset="utf-8">
<title>Danielle Brooke Interiors – Business Cards</title>
<link rel="stylesheet" href="https://fonts.googleapis.com/css2?family=Archivo:wght@700&family=Jost:wght@400&display=swap">
<style>
  :root {
    --bg: #e3deec;
    --paper: #ffffff;
    --navy: #182a7c;
    --gold: #b8923c;
    --blush: #f9d9d5;
    --blush-deep: #f3c6c0;
    --blush-soft: #fae6e3;
    --cream: #faf6f3;
  }
  * { margin: 0; padding: 0; box-sizing: border-box; }
  html, body { width: 1200px; height: 1200px; overflow: hidden; }
  body {
    background: var(--bg);
    font-family: "Jost", sans-serif;
    position: relative;
  }
  .card {
    position: absolute;
    left: 151px;
    width: 897px;
    height: 512px;
    background: var(--paper);
    overflow: hidden;
    box-shadow: 0 6px 18px rgba(40, 30, 70, 0.18);
  }
  .card--front { top: 64px; }
  .card--back { top: 624px; }
  .card__shapes { position: absolute; inset: 0; width: 100%; height: 100%; }

  .front__name {
    position: absolute; left: 80px; top: 98px;
    font-family: "Archivo", sans-serif; font-weight: 700;
    font-size: 49px; line-height: 1; color: var(--navy);
  }
  .front__role {
    position: absolute; left: 80px; top: 160px;
    font-size: 25px; letter-spacing: 0.5px; color: var(--gold);
  }
  .front__brand {
    position: absolute; left: 590px; top: 90px; width: 230px;
    font-size: 30px; line-height: 1.2; color: var(--navy);
    text-align: center;
  }
  .contact-list { position: absolute; left: 78px; top: 240px; list-style: none; }
  .contact-list li {
    display: flex; align-items: center; height: 54px;
    font-size: 25px; color: var(--navy);
  }
  .contact-list svg { width: 34px; height: 34px; margin-right: 24px; flex: none; }

  .back__brand-mark {
    position: absolute; left: 230px; top: 150px; width: 440px;
    font-size: 62px; line-height: 1.12; color: var(--navy);
    text-align: center;
  }
  .back__wordmark {
    position: absolute; left: 0; width: 920px; top: 382px;
    font-size: 36px; color: var(--gold); text-align: center;
  }
</style>
</head>
<body>

  <section class="card card--front" aria-label="Business card front">
    <svg class="card__shapes" viewBox="0 0 897 512" aria-hidden="true">
      <path d="M0 0 H205 C160 15 120 35 90 50 C60 65 25 68 0 62 Z" fill="var(--navy)"/>
      <path d="M628 512 C660 440 665 390 690 340 C720 285 800 262 897 258 V512 Z" fill="var(--blush)"/>
      <path d="M682 512 C700 450 705 410 730 370 C760 325 830 305 897 300 V512 Z" fill="var(--blush-soft)"/>
      <path d="M722 512 C735 460 740 430 760 405 C790 375 850 365 897 362 V512 Z" fill="var(--cream)"/>
    </svg>

    <h1 class="front__name">Danielle Brooke</h1>
    <p class="front__role">INTERIOR DESIGNER</p>
    <p class="front__brand">Danielle Brooke Interiors</p>

    <ul class="contact-list">
      <li>
        <svg viewBox="0 0 24 24" fill="none" stroke="var(--gold)" stroke-width="1.1"><path d="M5 3l3 0 1.5 4-2 1.5a11 11 0 0 0 6 6l1.5-2 4 1.5v3a2 2 0 0 1-2 2A16 16 0 0 1 3 5a2 2 0 0 1 2-2z"/><path d="M14 3a7 7 0 0 1 7 7M14 6a4 4 0 0 1 4 4"/></svg>
        123 456 7890
      </li>
      <li>
        <svg viewBox="0 0 24 24" fill="none" stroke="var(--gold)" stroke-width="1.1"><circle cx="12" cy="12" r="9"/><path d="M3 12h18M12 3c3 3 3 15 0 18M12 3c-3 3-3 15 0 18"/></svg>
        www.daniellebrooke.com
      </li>
      <li>
        <svg viewBox="0 0 24 24" fill="none" stroke="var(--gold)" stroke-width="1.1"><rect x="3" y="6" width="18" height="12"/><path d="M3 6l9 7 9-7M3 18l7-6M21 18l-7-6"/></svg>
        hello@daniellebrooke.com
      </li>
      <li>
        <svg viewBox="0 0 24 24" fill="none" stroke="var(--gold)" stroke-width="1.1"><path d="M12 22s-6-7-6-12a6 6 0 0 1 12 0c0 5-6 12-6 12z"/><circle cx="12" cy="10" r="2.5"/></svg>
        123 Anywhere St., Any City, ST 12345
      </li>
    </ul>
  </section>

  <section class="card card--back" aria-label="Business card back">
    <svg class="card__shapes" viewBox="0 0 897 512" aria-hidden="true">
      <circle cx="770" cy="20" r="120" fill="var(--navy)"/>
      <path d="M0 0 H640 C700 0 740 40 750 100 C760 180 750 260 720 330 C690 400 620 440 520 450 L0 460 Z" fill="var(--blush)"/>
      <path d="M0 350 C80 360 150 380 220 378 C320 375 420 350 480 380 C520 400 510 470 470 500 L0 512 Z" fill="var(--blush-deep)"/>
      <path d="M180 0 C190 60 170 120 130 150 C90 175 30 170 0 140" fill="none" stroke="var(--gold)" stroke-width="1.6"/>
    </svg>

    <p class="back__brand-mark">Danielle Brooke Interiors</p>
    <p class="back__wordmark">DANIELLE BROOKE INTERIORS</p>
  </section>

</body>
</html>
```